Request for Business Card Design

Hi. My name is Marlene, I am looking for a new business card design for my company, Quarrow Signal Instruments, LLC. I really like the design you did for Tarsel Venture and was hoping you could do something similar using our full logo and our mark. I am also open to any raised texture design using our mark. I have attached our full logo, which would need to be somewhere on the card, as well as the mark in both outline and full form, as well as our brand colors / guide. The card does not have to be white, as long as our logo and mark appear. I actually like darker colored business cards more, but am open to all options. If you are interested in working with me, please let me know. We would also take the business card design into letterhead design if you can do that.

```html
<!DOCTYPE html>
<html lang="en">
<head>
<meta charset="utf-8">
<title>Quarrow Signal Instruments – Business Card</title>
<link rel="stylesheet" href="https://fonts.googleapis.com/css2?family=Open+Sans:wght@400;600;700;800&display=swap">
<style>
  :root {
    --backdrop: #1f1f21;
    --card: #222226;
    --card-deep: #141416;
    --accent: #1a9ccc;
    --text: #f2f2f2;
    --muted: #3a3a3f;
  }
  * { box-sizing: border-box; margin: 0; padding: 0; }
  html, body { width: 1200px; height: 780px; overflow: hidden; background: var(--backdrop); }
  body { font-family: "Open Sans", Arial, sans-serif; color: var(--text); position: relative; }

  .card {
    position: absolute;
    width: 560px;
    height: 320px;
    background: var(--card);
    border-bottom: 5px solid var(--accent);
    border-left: 3px solid var(--accent);
    box-shadow: 0 18px 40px rgba(0,0,0,.55);
    overflow: hidden;
  }

  /* Back of card */
  .card-back { left: 60px; top: 60px; }
  .mark-field {
    position: absolute; inset: 0;
    background: linear-gradient(200deg, #6a6a70 0%, #3a3a3f 22%, var(--card-deep) 48%, #19191c 100%);
  }
  .back-brand {
    position: absolute; right: 30px; bottom: 26px;
    display: flex; align-items: center; gap: 8px;
    font-weight: 700; font-size: 10px; letter-spacing: .06em; text-transform: uppercase;
    color: var(--accent);
  }
  .back-brand .dot { width: 14px; height: 14px; border-radius: 50%; background: var(--accent); }

  /* Front of card */
  .card-front { left: 580px; top: 400px; }
  .brand {
    position: absolute; left: 34px; top: 34px;
    display: flex; align-items: center; gap: 12px;
    color: var(--text);
  }
  .brand .dot { width: 34px; height: 34px; border-radius: 50%; background: var(--accent); flex: none; }
  .brand-name {
    font-weight: 700; font-size: 15px; line-height: 1.15; letter-spacing: .08em; text-transform: uppercase;
  }

  .person { position: absolute; right: 40px; top: 26px; text-align: right; }
  .person-name { font-weight: 800; font-size: 34px; line-height: 1; color: var(--accent); }
  .person-role { font-weight: 600; font-size: 13px; margin-top: 2px; }
  .name-bar { position: absolute; right: 0; top: 22px; width: 14px; height: 52px; background: var(--accent); }

  .mark-emboss {
    position: absolute; right: 20px; top: 96px;
    width: 230px; height: 190px; border-radius: 50%;
    background: radial-gradient(circle at 45% 35%, #3b3b40 0%, #17171a 55%, #0c0c0e 100%);
  }

  .address {
    position: absolute; left: 40px; top: 150px;
    font-size: 13px; line-height: 1.35;
  }
  .contact {
    position: absolute; left: 40px; top: 196px;
    list-style: none; font-size: 13px; line-height: 1.3;
  }
  .contact li { display: flex; align-items: center; gap: 8px; height: 22px; }
  .contact svg { width: 14px; height: 14px; flex: none; }
</style>
</head>
<body>

  <section class="card card-back" aria-label="Card back">
    <div class="mark-field" role="img" aria-label="Repeating brand mark pattern fading from silver to black"></div>
    <div class="back-brand"><span class="dot"></span><span>Quarrow Signal Instruments</span></div>
  </section>

  <section class="card card-front" aria-label="Card front">
    <div class="brand">
      <span class="dot"></span>
      <span class="brand-name">Quarrow Signal<br>Instruments</span>
    </div>

    <div class="person">
      <div class="person-name">Marlene</div>
      <div class="person-role">Director</div>
    </div>
    <div class="name-bar"></div>

    <div class="mark-emboss" role="img" aria-label="Large embossed brand mark in black"></div>

    <p class="address">1180 Ridgeline Parkway &bull;<br>Loveland, CO 80538</p>

    <ul class="contact">
      <li>
        <svg viewBox="0 0 16 16" fill="var(--accent)"><path d="M3.5 1.5l2.5 0 1 3.5-1.8 1.2a8 8 0 0 0 4.6 4.6l1.2-1.8 3.5 1v2.5a1.5 1.5 0 0 1-1.5 1.5A12 12 0 0 1 2 3a1.5 1.5 0 0 1 1.5-1.5z"/></svg>
        +001 303 555 0142
      </li>
      <li>
        <svg viewBox="0 0 16 16" fill="var(--accent)"><rect x="4" y="1" width="8" height="5"/><rect x="1" y="6" width="14" height="8" rx="1"/><rect x="4" y="9" width="8" height="2" fill="var(--card)"/></svg>
        +001 303 555 0187
      </li>
      <li>
        <svg viewBox="0 0 16 16" fill="none" stroke="var(--accent)" stroke-width="1.6"><circle cx="8" cy="8" r="6.5"/><ellipse cx="8" cy="8" rx="2.8" ry="6.5"/><path d="M1.5 8h13"/></svg>
        www.quarrowsignal.com
      </li>
      <li>
        <svg viewBox="0 0 16 16" fill="none" stroke="var(--accent)" stroke-width="1.6"><rect x="1.5" y="3.5" width="13" height="9" rx="1"/><path d="M1.5 4l6.5 5 6.5-5"/></svg>
        info@quarrowsignal.com
      </li>
    </ul>
  </section>

</body>
</html>
```